Commercial, Public Works, Contractor needs a modern web design

We are a General and Engineering contracting firm with vast experience in our industry. Our focus is on Commercial, Tenant Improvement, Restaurants, and Public Works. We are opening a new business and would like that excitement and energy to show through the new web design. The colors we like are black, red and grey, we are open to color ideas. Attached is our logo design.

Industry/Entity Type

Restaurant

```html
<!DOCTYPE html>
<html lang="en">
<head>
<meta charset="utf-8">
<title>RK Holland, Inc. — General Contractor and Engineer</title>
<link href="https://fonts.googleapis.com/css2?family=Open+Sans:wght@300;400;600;700&display=swap" rel="stylesheet">
<style>
:root{
  --red:#a3121b;
  --topbar:#1b5e87;
  --ink:#333333;
  --muted:#666666;
  --panel:#dcd8d8;
  --footer:#6e6a6b;
  --white:#ffffff;
  --blue:#2f6fa8;
  --maroon:#6b1736;
  --green:#2e5a45;
}
*{margin:0;padding:0;box-sizing:border-box}
html,body{width:814px;height:1200px;overflow:hidden;background:var(--white)}
body{font-family:"Open Sans",Arial,sans-serif;color:var(--ink);position:relative}
.abs{position:absolute}
.hero{left:0;top:0;width:814px;height:450px;background:linear-gradient(100deg,#2b3640 0%,#3f4c58 40%,#6a7480 62%,#c9a37a 80%,#8a9099 100%)}
.topbar{left:0;top:0;width:814px;height:21px;background:var(--topbar)}
.topbar .signup{position:absolute;right:68px;top:5px;font-size:8px;color:var(--white)}
.topbar svg{position:absolute;left:655px;top:5px}
.logo{left:67px;top:0;width:166px;height:102px;background:var(--white);display:flex;align-items:center;justify-content:center;gap:6px}
.logo .mark{width:14px;height:14px;border-radius:50%;background:var(--red)}
.logo .name{font-weight:700;font-size:15px;color:var(--red)}
.nav{left:296px;top:48px;display:flex;gap:27px;font-size:11px;font-weight:600;color:var(--white)}
.nav .current{text-decoration:underline;color:#dfe6ee}
.login{left:690px;top:42px;width:57px;height:26px;background:#eeeeee;color:var(--red);font-size:11.5px;font-weight:600;display:flex;align-items:center;justify-content:center}
.headline{left:66px;top:210px;font-size:43px;font-weight:600;color:var(--white);letter-spacing:.5px;white-space:nowrap}
.sub{left:96px;top:271px;width:400px;text-align:center;color:var(--white);font-size:20.5px;font-weight:600;line-height:28px;white-space:nowrap}
.dots{left:266px;top:367px;display:flex;gap:8px}
.dots span{width:9px;height:9px;border-radius:50%;background:var(--white)}
.dots span.on{background:#e0141c}
.section-title{width:814px;text-align:center;font-size:18px;font-weight:400;color:var(--ink)}
.rule{left:372px;width:70px;height:1px;background:#444}
.intro{left:190px;width:434px;text-align:center;font-size:7.8px;font-weight:300;line-height:14px;color:var(--muted)}
.service{top:550px;width:150px;text-align:center}
.service svg{display:block;margin:0 auto}
.service .label{margin-top:8px;font-size:11px;font-weight:600;color:#444}
.projects{left:0;top:654px;width:814px;height:308px;background:var(--panel)}
.project{top:754px;width:164px}
.project .photo{height:82px}
.project .bar{height:4px;background:var(--red)}
.project h3{margin-top:9px;text-align:center;font-size:11px;font-weight:600;color:#222}
.project p{margin-top:3px;text-align:center;font-size:7.6px;font-weight:300;line-height:14px;color:var(--muted);letter-spacing:-.1px}
.btn{left:347px;top:910px;width:117px;height:28px;background:var(--red);color:var(--white);font-size:11px;font-weight:600;display:flex;align-items:center;justify-content:center;gap:10px;border-radius:2px}
.col h4{font-size:11px;font-weight:600;color:var(--red);margin-bottom:10px}
.col .line{font-size:10px;line-height:16px;color:var(--ink)}
.col b{font-weight:600}
.col .post{font-size:10px;line-height:15px;color:var(--ink);margin-bottom:8px}
.col .date{font-size:18px;color:var(--ink);margin-bottom:10px}
.col .body{font-size:8px;font-weight:300;line-height:14px;color:var(--muted)}
.col .more{display:block;margin-top:8px;font-size:11px;color:#777;text-decoration:underline}
.divider{left:267px;top:984px;width:1px;height:168px;background:#ccc}
.social{display:flex;gap:6px;margin-top:12px}
.social span{width:25px;height:25px;border:1.5px solid #555;border-radius:50%;display:flex;align-items:center;justify-content:center}
.social span i{width:9px;height:9px;border-radius:50%;background:#555}
.bottom{left:0;top:1154px;width:814px;height:46px;background:var(--footer);color:var(--white);font-size:8px;padding:19px 0 0 66px}
</style>
</head>
<body>
<div class="abs hero" role="img" aria-label="Smiling construction engineer in a hard hat and safety vest holding plans on a building site"></div>
<div class="abs topbar">
  <svg width="10" height="10" viewBox="0 0 10 10"><circle cx="4" cy="4" r="3" fill="none" stroke="#fff" stroke-width="1.6"/><line x1="6.2" y1="6.2" x2="9.3" y2="9.3" stroke="#fff" stroke-width="1.8"/></svg>
  <span class="signup">SIGN UP / REGISTER</span>
</div>
<div class="abs logo"><span class="mark"></span><span class="name">RK HOLLAND, INC.</span></div>
<nav class="abs nav"><span class="current">HOME</span><span>SERVICES</span><span>RECENT PROJECTS</span><span>BLOG</span><span>CONTACT</span></nav>
<div class="abs login">LOGIN</div>
<h1 class="abs headline">CREATING THE FUTURE</h1>
<div class="abs sub">WE IMPROVE PEOPLE’S LIFE.<br>BEST PERFORMANCE OVER THE YEARS</div>
<div class="abs dots"><span></span><span></span><span></span><span class="on"></span></div>

<h2 class="abs section-title" style="top:464px">WHAT WE DO</h2>
<div class="abs rule" style="top:495px"></div>
<p class="abs intro" style="top:506px">Lorem ipsum dolor sit amet, consectetuer adipiscing elit. Praesent vestibulum molestie lacus. Aenean nonummy hendrerit mauris. Phasellus porta. Fusce suscipit varius mi.</p>

<div class="abs service" style="left:86px">
  <svg width="78" height="60" viewBox="0 0 78 60" aria-label="Laptop with gear">
    <rect x="9" y="6" width="60" height="40" rx="3" fill="none" stroke="var(--red)" stroke-width="4"/>
    <rect x="2" y="48" width="74" height="6" rx="2" fill="var(--red)"/>
    <g fill="var(--red)">
      <circle cx="39" cy="26" r="11"/>
      <rect x="36" y="10" width="6" height="32"/>
      <rect x="23" y="23" width="32" height="6"/>
      <rect x="36" y="10" width="6" height="32" transform="rotate(45 39 26)"/>
      <rect x="36" y="10" width="6" height="32" transform="rotate(-45 39 26)"/>
    </g>
    <circle cx="39" cy="26" r="5" fill="#fff"/>
  </svg>
  <div class="label">Consectetuer adipiscing</div>
</div>
<div class="abs service" style="left:250px">
  <svg width="78" height="60" viewBox="0 0 78 60" aria-label="Hard hat">
    <path d="M15 40 A24 24 0 0 1 63 40 Z" fill="var(--blue)"/>
    <rect x="36" y="12" width="6" height="22" fill="#fff"/>
    <rect x="8" y="40" width="62" height="7" rx="3" fill="var(--blue)"/>
    <rect x="20" y="51" width="38" height="4" rx="2" fill="var(--blue)"/>
  </svg>
  <div class="label">Praesent vestibulum</div>
</div>
<div class="abs service" style="left:403px">
  <svg width="78" height="60" viewBox="0 0 78 60" aria-label="Wrench">
    <g transform="rotate(45 39 30)" fill="var(--maroon)">
      <rect x="35" y="12" width="8" height="40" rx="3"/>
      <path d="M27 4 h8 v8 h8 v-8 h8 v10 a12 12 0 0 1 -24 0 Z"/>
    </g>
  </svg>
  <div class="label">Hendrerit mauris</div>
</div>
<div class="abs service" style="left:565px">
  <svg width="90" height="60" viewBox="0 0 90 60" aria-label="Monitor with chart and gears">
    <rect x="4" y="4" width="82" height="40" rx="3" fill="none" stroke="var(--green)" stroke-width="4"/>
    <g fill="var(--green)">
      <rect x="14" y="26" width="6" height="12"/><rect x="24" y="18" width="6" height="20"/><rect x="34" y="22" width="6" height="16"/>
      <circle cx="58" cy="22" r="7"/><circle cx="74" cy="18" r="5"/>
      <rect x="38" y="44" width="14" height="8"/>
      <rect x="28" y="52" width="34" height="5" rx="2"/>
    </g>
    <circle cx="58" cy="22" r="3" fill="#fff"/><circle cx="74" cy="18" r="2" fill="#fff"/>
  </svg>
  <div class="label">Fusce suscipit</div>
</div>

<div class="abs projects"></div>
<h2 class="abs section-title" style="top:670px">OUR LATEST PROJECTS</h2>
<div class="abs rule" style="top:701px"></div>
<p class="abs intro" style="top:712px">Cum sociis natoque penatibus et magnis dis parturient montes, nascetur ridiculus mus. Nulla dui. Fusce feugiat malesuada odio. Morbi nunc odio, gravida at, cursus.</p>
<div class="abs project" style="left:67px"><div class="photo" role="img" aria-label="White commercial office building with palm trees" style="background:linear-gradient(180deg,#4f86c6,#dfe4e8 55%,#6d7a5a)"></div><div class="bar"></div><h3>COMMERCIAL</h3><p>Gratuitous octopus niacodiumtimate. Quote meon an estimate et interruptus stadium.</p></div>
<div class="abs project" style="left:239px"><div class="photo" role="img" aria-label="Building under construction at dusk" style="background:linear-gradient(180deg,#2c3138,#40454b)"></div><div class="bar"></div><h3>TENANT IMPROVEMENT</h3><p>Gratuitous octopus niacodiumtimate. Quote meon an estimate et interruptus stadium.</p></div>
<div class="abs project" style="left:411px"><div class="photo" role="img" aria-label="Illuminated restaurant building at evening" style="background:linear-gradient(180deg,#3d4f7a,#8d6a4a 60%,#c98a3c)"></div><div class="bar"></div><h3>RESTAURANTS</h3><p>Gratuitous octopus niacodiumtimate. Quote meon an estimate et interruptus stadium.</p></div>
<div class="abs project" style="left:583px"><div class="photo" role="img" aria-label="Concrete highway bridges seen from below" style="background:linear-gradient(90deg,#5a5e55,#8fb0d8 50%,#5a5e55)"></div><div class="bar"></div><h3>PUBLIC WORKS</h3><p>Gratuitous octopus niacodiumtimate. Quote meon an estimate et interruptus stadium.</p></div>
<div class="abs btn">VIEW ALL <svg width="10" height="10" viewBox="0 0 10 10"><path d="M1 5h6M4.5 1.8 8 5 4.5 8.2" fill="none" stroke="#fff" stroke-width="2"/></svg></div>

<div class="abs col" style="left:66px;top:984px;width:190px">
  <h4>CONTACT US</h4>
  <div class="line">mail@rkholland.org</div>
  <div class="line" style="margin-top:2px"><b>Phone:</b><br>+1 555 010 2846 (555-order)</div>
  <div class="line" style="margin-top:2px"><b>Location:</b><br>412 Fenwick Lane Glasgow,<br>G12 7QT.</div>
  <div class="social">
    <span><i></i></span><span><i></i></span>
    <span><svg width="13" height="10" viewBox="0 0 13 10"><rect x="0.5" y="0.5" width="12" height="9" rx="1" fill="#555"/><path d="M1 1l5.5 4.5L12 1" fill="none" stroke="#fff" stroke-width="1.2"/></svg></span>
    <span><i></i></span><span><i></i></span>
  </div>
</div>
<div class="abs divider"></div>
<div class="abs col" style="left:333px;top:984px;width:180px">
  <h4>FROM THE BLOG</h4>
  <div class="post">Praesent vestibulum molestie lacus. Aenean nonummy hendrerit</div>
  <div class="body">Lorem ipsum dolor sit amet, conse adipiscing elit. Praesent vestibulum molestie lacus. Aenean nonummy hendrerit mauris. Phasellus porta. Fusce suscipit varius mi. Cum sociis natoque penatibus et magnis dis.</div>
  <a class="more">Read more</a>
</div>
<div class="abs col" style="left:577px;top:984px;width:180px">
  <h4>NEWS &amp; EVENTS</h4>
  <div class="date">04/02/2015</div>
  <div class="body">Lorem ipsum dolor sit amet, conse adipiscing elit. Praesent vestibulum molestie lacus. Aenean nonummy hendrerit mauris. Phasellus porta. Fusce suscipit varius mi. Cum sociis natoque penatibus et magnis dis.</div>
  <a class="more">Read more</a>
</div>
<footer class="abs bottom">RK HOLLAND General Engineering © 2015 Privacy policy. Terms of use</footer>
</body>
</html>
```